Bold, Modern, Clean "Kestrelwaymassage.com" website

Why we stand out?
We are a male and female mobile massage team. Our names are Paul and Lina. 
Kestrel Way is a Seattle based mobile massage service. Our massage is offered to the community with a goal of facilitating balance within each individual. We specialize in integrated Pain management, and sports/medical massage therapy. Every client's first assessment is attended by our male and female massage therapist team. Depending on the goals identified for an individual determines which therapist will be assigned to provide treatment, if not both.

Our passion...
Here at Kestrel Way, we have a great passion for Postural Resoration and how it is integrated into an individual's Massage treatment. We pride ourselves in being natural facilitators of healing, which takes the ego of the therapist out of the client's healing process. We strive to deliver the best massage possible by including modalities such as Neuromuscular, Myofascial release, spontaneous muscle release, postural restoration, orthopedic, and medical massage.

Our education...

We are both Graduates of Venmora, school of massage therapy. We have continuing education in medical massage, myofacial release, trigger point therapy, postural restoration, anatomy, and spontaneous muscle release. Lina is also a Certified Yoga Instructor, which amplifies her experience with flexibility and strength as it pertains to each individual. Paul's passion is Massage, stretching, and strength training to encourage postural restoration and realignment.

Our rates-

Our rates are $75/ 60 minutes, $95/ 90 minutes, and $120/ 120 minutes.

Education-
Both Lina and I worked as behavioral health professionals that specialized in life skills mentoring for youth who had experienced different types of trauma. This led us both to want to help others in a different environment, where individuals can be empowered to take responsibility over their own healing. To us, massage is a type of manipulation physical therapy, that encourages healing on many levels.

Advice to any massage client-
The most important thing to 'us', as Licenced providers is to get you on to our table to show you our skills. But a good therapist never forgets that it's not about what we do for you, but what we can facilitate for you. Your health and healing has nothing to do with us. It is yours, not ours. Identify what your goals are with any Therapist, and know what the end looks like. Progress should be tangible, such as range of motion, and decreased pain.

Lina and Paul at Kestrel Way are awesome! I recently had open heart surgery, and Lina worked on me to increase my range of motion while helping with the pinched nerve from my arm being in the same position for so long during my surgery. My wife drives a lot for work, and Paul has helped decrease her neck and lower back pain immensely. They are seriously the best therapists I have ever worked with. I would recommend them to anyone who needs anything from stress relief to a medical massage treatment. They are professional, up beat, easy going, and always on time. And, I love that they meet us where ever we like! We did a staycation recently, where they came to our hotel to give us relaxation massages. Although usually they come to our home, where we focus on pain related issues. We will continue to work with them for a long, long time.

Target Market(s)

Mobile massage therapy clients

Industry/Entity Type

Massage Therapy

Coding

Coded - Design and coding required

Number of Pages Required

1 page

Font styles to use
Serif
Sans Serif

Requirements
Must have
• Please add or remove any information that would help the presentation of our website. Our logo is posted below, please include into the website.
• Please include a contact field that includes, kestrelwaymassage@fernmail.net,
• (206) 555-0148
• We have also included our own stock photos, as well as a photo of Paul and Lina. Please include a cropped photo of both massage therapists.

```html
<!DOCTYPE html>
<html lang="en">
<head>
<meta charset="utf-8">
<title>Kestrel Way – Mobile Massage</title>
<link href="https://fonts.googleapis.com/css2?family=Lato:wght@400;700&family=Arvo:wght@700&family=Cormorant+Garamond:ital,wght@1,600&family=Roboto+Condensed:wght@300&display=swap" rel="stylesheet">
<style>
:root{
  --red:#b94a4a;
  --red-light:#c96060;
  --orange:#e9954a;
  --navy:#262261;
  --blue:#1029a8;
  --ink:#333333;
  --muted:#8a8a8a;
  --grey-bg:#f2f2f2;
  --line:#e6b7a8;
  --white:#ffffff;
}
*{margin:0;padding:0;box-sizing:border-box}
html,body{width:1200px;height:2406px;overflow:hidden}
body{position:relative;background:var(--white);font-family:'Lato',sans-serif;color:var(--ink)}
.abs{position:absolute}

/* top bar */
.quick-btn{left:82px;top:18px;width:151px;height:35px;border-radius:18px;background:var(--blue);color:var(--white);font:700 14px 'Lato',sans-serif;display:flex;align-items:center;justify-content:center;gap:8px}
.top-contact{right:82px;top:24px;font-size:14px;display:flex;gap:26px;align-items:center}
.top-contact span{display:flex;gap:8px;align-items:center}

/* nav */
.nav{left:0;top:72px;width:1200px;height:56px;background:var(--red);border-top:1px dashed rgba(255,255,255,.5);border-bottom:1px dashed rgba(255,255,255,.5);box-shadow:inset 0 3px 0 var(--red),inset 0 -3px 0 var(--red)}
.nav-item{top:90px;color:var(--white);font-size:14px;letter-spacing:.5px}
.nav-item.active{color:#f6c4a0}
.nav-star{top:88px;color:var(--white);font-size:12px}
.brand-mark{left:528px;top:24px;width:144px;height:144px;border-radius:50%;background:var(--blue);border:5px solid var(--white);box-shadow:0 0 0 2px var(--blue);display:flex;align-items:center;justify-content:center;text-align:center;color:var(--white);font:700 24px/1.1 'Lato',sans-serif;z-index:5}

/* hero */
.hero{left:0;top:128px;width:1200px;height:534px;background:linear-gradient(90deg,#e8ddd2 0%,#f7f3ef 30%,#fbf6f2 50%,#f3d9c8 75%,#f6e6da 100%)}
.hero-title{left:289px;top:198px;font:italic 600 64px/1 'Cormorant Garamond',serif;color:var(--red);letter-spacing:2px}
.hero-title.second{top:270px;color:var(--orange);font-style:normal;font-family:'Arvo',serif;font-size:56px;font-weight:700;letter-spacing:0}
.hero-sub{left:360px;top:344px;font-size:26px;color:#222}

/* section titles */
.sec-title{left:0;width:1200px;text-align:center;font:700 28px 'Arvo',serif;color:var(--red)}
.sec-title b{color:var(--blue)}
.divider{left:498px;width:204px;height:16px}

/* about */
.about-text{left:80px;top:778px;width:1040px;text-align:center;font-size:12.5px;line-height:20px;color:#333}
.about-photo{left:64px;top:866px;width:481px;height:313px;background:radial-gradient(ellipse at 50% 55%,#e5b7c2 0%,#f4e3e6 45%,#ffffff 75%)}
.feature-icon{left:607px;width:78px;height:78px;border-radius:50%;background:var(--red);border:4px solid var(--white);box-shadow:0 0 0 2px #d9d9d9}
.feature-title{left:717px;font:700 17px 'Lato',sans-serif;color:var(--red)}
.feature-text{left:718px;width:398px;font-size:12px;line-height:20px;color:var(--muted)}
.read-more{left:1037px;font:700 11px 'Lato',sans-serif;color:var(--blue);text-decoration:underline}

/* prices */
.prices{left:0;top:1184px;width:1200px;height:532px;background:var(--grey-bg);border-top:3px solid #dcdcdc;border-bottom:3px solid #dcdcdc}
.price-card{top:1318px;width:241px;height:355px;background:var(--white);border:1px solid #cfcfcf;box-shadow:inset 0 0 0 4px var(--white),inset 0 0 0 5px #e3e3e3}
.price-head{left:5px;top:5px;right:5px;height:128px;background:linear-gradient(180deg,#c56060,#b94a4a);color:var(--white);text-align:center;font:300 29px 'Roboto Condensed',sans-serif;padding-top:22px}
.price-badge{left:58px;top:76px;width:122px;height:122px;border-radius:50%;background:var(--white);border:4px solid #f0f0f0;display:flex;align-items:center;justify-content:center;font:700 36px 'Lato',sans-serif;color:var(--blue)}
.price-name{left:0;top:201px;width:100%;text-align:center;font:700 19px 'Lato',sans-serif;color:var(--blue)}
.price-text{left:18px;top:232px;width:203px;text-align:center;font-size:12px;line-height:17px;color:#666}
.price-btn{left:67px;top:295px;width:106px;height:33px;background:var(--red-light);color:var(--white);font-size:13px;display:flex;align-items:center;justify-content:center}

/* testimonials */
.avatar{left:548px;top:1853px;width:106px;height:106px;border-radius:50%;border:2px dashed #9a9a9a;padding:6px}
.avatar div{width:100%;height:100%;border-radius:50%;background:linear-gradient(180deg,#e9edf2,#b9c2cc)}
.quote{left:290px;top:1978px;width:700px;text-align:center;font-size:12.5px;line-height:22px;color:#333}
.quote-mark{left:258px;top:1962px;font:700 48px Georgia,serif;color:#f1d6cf}
.quote-name{left:0;top:2024px;width:1200px;text-align:center;font:700 13px 'Lato',sans-serif}
.dot{top:2066px;width:12px;height:12px;border-radius:50%;background:var(--red)}
.dot.on{background:var(--navy)}
.deco-left{left:0;top:1970px;width:270px;height:144px;background:linear-gradient(90deg,#9a95b5,#d9d6e6 60%,rgba(255,255,255,0))}
.deco-right{left:900px;top:1940px;width:300px;height:174px;background:linear-gradient(270deg,#e8e8e6,#f1e6e6 60%,rgba(255,255,255,0))}

/* footer */
.footer{left:0;top:2114px;width:1200px;height:257px;background:var(--navy);color:var(--white)}
.f-head{top:2150px;font-size:17px;color:var(--white);border-bottom:1px dashed rgba(255,255,255,.4);padding-bottom:9px}
.f-links{left:82px;top:2195px;list-style:none;font-size:12.5px;line-height:24px;color:var(--white)}
.f-links li::before{content:"›";margin-right:10px}
.f-vline{top:2150px;width:0;height:190px;border-left:1px dashed rgba(255,255,255,.3)}
.f-input{left:313px;width:224px;height:22px;background:var(--white);border-radius:3px;color:#333;font-size:12px;padding:3px 8px}
.f-submit{left:313px;top:2307px;width:62px;height:22px;background:var(--red-light);color:var(--white);font-size:12px;display:flex;align-items:center;justify-content:center}
.f-contact{left:642px;font-size:12.5px;line-height:17px;display:flex;gap:12px;color:var(--white)}
.f-brand{left:985px;top:2154px;width:128px;height:128px;border-radius:50%;background:#3a3a8a;border:3px solid #6c6cb0;display:flex;align-items:center;justify-content:center;text-align:center;font:700 20px/1.1 'Lato',sans-serif;color:var(--white)}
.f-social{top:2300px;width:32px;height:32px;border-radius:50%;background:var(--red-light)}
.bottom-bar{left:0;top:2371px;width:1200px;height:35px;background:var(--red);color:var(--white);font-size:11.5px}
</style>
</head>
<body>

<!-- Top bar -->
<div class="abs quick-btn">
  <svg width="12" height="12" viewBox="0 0 12 12"><rect x="1" y="2" width="10" height="9" fill="none" stroke="#fff" stroke-width="1.4"/><line x1="1" y1="5" x2="11" y2="5" stroke="#fff" stroke-width="1.4"/></svg>
  QUICK INQUERY
</div>
<div class="abs top-contact">
  <span><svg width="14" height="10" viewBox="0 0 14 10"><rect x=".7" y=".7" width="12.6" height="8.6" fill="none" stroke="#1029a8" stroke-width="1.3"/><polyline points="1,1 7,6 13,1" fill="none" stroke="#1029a8" stroke-width="1.3"/></svg>kestrelwaymassage@fernmail.net</span>
  <span><svg width="14" height="14" viewBox="0 0 14 14"><path d="M3 1 L5.5 4 L4 5.5 Q5.5 8.5 8.5 10 L10 8.5 L13 11 L11 13 Q5 12 1 3 Z" fill="#1029a8"/></svg>(206) 555-0148</span>
</div>

<!-- Navigation -->
<div class="abs nav"></div>
<div class="abs nav-item active" style="left:80px">HOME</div>
<div class="abs nav-star" style="left:168px">★</div>
<div class="abs nav-item" style="left:218px">ABOUT US</div>
<div class="abs nav-star" style="left:332px">★</div>
<div class="abs nav-item" style="left:383px">SERVICES</div>
<div class="abs nav-star" style="left:496px">★</div>
<div class="abs nav-star" style="left:694px">★</div>
<div class="abs nav-item" style="left:728px">PRICES</div>
<div class="abs nav-star" style="left:808px">★</div>
<div class="abs nav-item" style="left:839px">PHOTO GALLERY</div>
<div class="abs nav-star" style="left:989px">★</div>
<div class="abs nav-item" style="left:1023px">CONTACT US</div>

<!-- Hero -->
<div class="abs hero" role="img" aria-label="Spa still life with towels, candle, stones and flowers beside a woman relaxing during a massage"></div>
<div class="abs hero-title">MASSAGE</div>
<div class="abs hero-title second">THERAPY</div>
<div class="abs hero-sub">We come to you</div>

<div class="abs brand-mark">Kestrel<br>Way</div>

<!-- About -->
<div class="abs sec-title" style="top:690px">ABOUT <b>US</b></div>
<svg class="abs divider" style="top:738px" viewBox="0 0 204 16"><line x1="0" y1="6" x2="82" y2="6" stroke="#e6b7a8"/><line x1="0" y1="10" x2="82" y2="10" stroke="#e6b7a8"/><line x1="122" y1="6" x2="204" y2="6" stroke="#e6b7a8"/><line x1="122" y1="10" x2="204" y2="10" stroke="#e6b7a8"/><circle cx="102" cy="8" r="8" fill="#333"/></svg>
<p class="abs about-text">We are a male and female mobile massage team. Our names are Paul and Lina. Kestrel Way is a Seattle based mobile massage service. Our massage is offered to the community with a goal of facilitating balance within each individual. We specialize in integrated Pain management, and sports/medical massage therapy. Every client's first assessment is attended by our male and female massage therapist team. Depending on the goals identified for an individual determines which therapist will be assigned to provide treatment, if not both.</p>

<div class="abs about-photo" role="img" aria-label="Pink daisies and stacked massage stones with scattered petals"></div>

<div class="abs feature-icon" style="top:859px"></div>
<div class="abs feature-title" style="top:856px">Why We Stand Out?</div>
<p class="abs feature-text" style="top:882px">Kestrel Way is a Seattle based mobile massage service. Our massage is offered to the community with a goal of facilitating balance within each individual.</p>
<div class="abs read-more" style="top:934px">Read More &nbsp;»</div>

<div class="abs feature-icon" style="top:963px"></div>
<div class="abs feature-title" style="top:961px">Our Passion.</div>
<p class="abs feature-text" style="top:984px">Here at Kestrel Way, we have a great passion for Postural Resoration and how it is integrated into an individual's Massage treatment. We pride ourselves in being natural</p>
<div class="abs read-more" style="top:1033px">Read More &nbsp;»</div>

<div class="abs feature-icon" style="top:1065px"></div>
<div class="abs feature-title" style="top:1061px">Our Education.</div>
<p class="abs feature-text" style="top:1084px">We are both Graduates of Venmora, school of massage therapy. We have continuing education in medical massage, myofacial release, trigger point therapy, postural restoration, anatomy</p>
<div class="abs read-more" style="top:1133px">Read More &nbsp;»</div>

<!-- Prices -->
<div class="abs prices"></div>
<div class="abs sec-title" style="top:1216px">OUR <b>PRICES</b></div>
<svg class="abs divider" style="top:1264px" viewBox="0 0 204 16"><line x1="0" y1="6" x2="82" y2="6" stroke="#e6b7a8"/><line x1="0" y1="10" x2="82" y2="10" stroke="#e6b7a8"/><line x1="122" y1="6" x2="204" y2="6" stroke="#e6b7a8"/><line x1="122" y1="10" x2="204" y2="10" stroke="#e6b7a8"/><circle cx="102" cy="8" r="8" fill="#333"/></svg>

<div class="abs price-card" style="left:80px">
  <div class="abs price-head">60 minutes</div>
  <div class="abs price-badge">$75</div>
  <div class="abs price-name">MASSAGE THERAPY</div>
  <p class="abs price-text">Both Lina and I worked as behavioral health professionals that specialized in life skills mentoring for</p>
  <div class="abs price-btn">Read More</div>
</div>
<div class="abs price-card" style="left:346px">
  <div class="abs price-head">90 minutes</div>
  <div class="abs price-badge">$95</div>
  <div class="abs price-name">MASSAGE THERAPY</div>
  <p class="abs price-text">Both Lina and I worked as behavioral health professionals that specialized in life skills mentoring for</p>
  <div class="abs price-btn">Read More</div>
</div>
<div class="abs price-card" style="left:613px">
  <div class="abs price-head">120 minutes</div>
  <div class="abs price-badge">$120</div>
  <div class="abs price-name">MASSAGE THERAPY</div>
  <p class="abs price-text">Both Lina and I worked as behavioral health professionals that specialized in life skills mentoring for</p>
  <div class="abs price-btn">Read More</div>
</div>
<div class="abs price-card" style="left:879px">
  <div class="abs price-head">150 minutes</div>
  <div class="abs price-badge">$150</div>
  <div class="abs price-name">MASSAGE THERAPY</div>
  <p class="abs price-text">Both Lina and I worked as behavioral health professionals that specialized in life skills mentoring for</p>
  <div class="abs price-btn">Read More</div>
</div>

<!-- Testimonials -->
<div class="abs sec-title" style="top:1750px">CLIENT <b>TESTIMONIALS</b></div>
<svg class="abs divider" style="top:1797px" viewBox="0 0 204 16"><line x1="0" y1="6" x2="82" y2="6" stroke="#e6b7a8"/><line x1="0" y1="10" x2="82" y2="10" stroke="#e6b7a8"/><line x1="122" y1="6" x2="204" y2="6" stroke="#e6b7a8"/><line x1="122" y1="10" x2="204" y2="10" stroke="#e6b7a8"/><circle cx="102" cy="8" r="8" fill="#333"/></svg>
<div class="abs deco-left" role="img" aria-label="Rolled lavender towel with stacked stones and lavender sprigs"></div>
<div class="abs deco-right" role="img" aria-label="Folded white towels with candles and an orchid"></div>
<div class="abs avatar" role="img" aria-label="Portrait of the reviewing client"><div></div></div>
<div class="abs quote-mark">“</div>
<p class="abs quote">The most important thing to 'us', as Licenced providers is to get you on to our table to show you our skills. But a good therapist never forgets that it's not about what we do for you, but what we can facilitate for you.</p>
<div class="abs quote-name">Ms. Dana Ferrel</div>
<div class="abs dot" style="left:571px"></div>
<div class="abs dot on" style="left:594px"></div>
<div class="abs dot" style="left:618px"></div>

<!-- Footer -->
<div class="abs footer"></div>
<div class="abs f-head" style="left:82px;width:125px">Quick Links</div>
<ul class="abs f-links">
  <li>Home</li><li>About US</li><li>Services</li><li>Prices</li><li>Photo Gallery</li><li>Contact Us</li>
</ul>
<div class="abs f-vline" style="left:257px"></div>

<div class="abs f-head" style="left:311px;width:226px;border-bottom:none">Quick Inquiry</div>
<div class="abs f-input" style="top:2201px">Name</div>
<div class="abs f-input" style="top:2230px">Email</div>
<div class="abs f-input" style="top:2259px;height:40px">Message</div>
<div class="abs f-submit">Submit</div>
<div class="abs f-vline" style="left:589px"></div>

<div class="abs f-head" style="left:642px;width:236px">Contact Details</div>
<div class="abs f-contact" style="top:2194px">
  <svg width="10" height="14" viewBox="0 0 10 14"><path d="M5 0 A5 5 0 0 1 10 5 C10 9 5 14 5 14 C5 14 0 9 0 5 A5 5 0 0 1 5 0 Z" fill="#fff"/><circle cx="5" cy="5" r="2" fill="#262261"/></svg>
  <span>Lorem ipsum dolor sit amet,<br>consectetuer adipiscing elit, sed<br>diam nonummy nibh .</span>
</div>
<div class="abs f-contact" style="top:2264px">
  <svg width="13" height="13" viewBox="0 0 14 14"><path d="M3 1 L5.5 4 L4 5.5 Q5.5 8.5 8.5 10 L10 8.5 L13 11 L11 13 Q5 12 1 3 Z" fill="#fff"/></svg>
  <span>(206) 555-0148</span>
</div>
<div class="abs f-contact" style="top:2296px">
  <svg width="13" height="10" viewBox="0 0 14 10"><rect x=".7" y=".7" width="12.6" height="8.6" fill="none" stroke="#fff" stroke-width="1.3"/><polyline points="1,1 7,6 13,1" fill="none" stroke="#fff" stroke-width="1.3"/></svg>
  <span>kestrelwaymassage@fernmail.net</span>
</div>
<div class="abs f-vline" style="left:927px"></div>

<div class="abs f-brand">Kestrel<br>Way</div>
<div class="abs f-social" style="left:1003px"></div>
<div class="abs f-social" style="left:1043px"></div>
<div class="abs f-social" style="left:1083px"></div>

<div class="abs bottom-bar">
  <span class="abs" style="left:82px;top:11px">Copyright © 2015 kestrelwaymassage &nbsp;| All Right Reserved.</span>
  <span class="abs" style="left:895px;top:11px">Terms &amp; Conditions &nbsp;&nbsp;&nbsp; | &nbsp;&nbsp;&nbsp; Privacy Policy</span>
</div>

</body>
</html>
```